Letterhead and email signature block for school

We are a Remote School in the North West of Western Australia and I want to take our logo and use that to create a professional letter head and email signature block. A sample signature block is attached. For the Letterhead; The logo is also attached. I like the Orange and black combination of the logo, needs to include motto plus the following contact details;
PMB 4 KARRAWIN WA
Phone: (08) 9170 3158
Fax: (08) 9170 3206
ABN: 41 287 519 302

The email signature block needs to have the following;
Dale Owen Wrenfield
Principal
Tern Ridge Hill RCS
Phone: (08) 9170 3158
Fax: (08) 9170 3206
Mobile: 0488 613 947
Email: Dale.Wrenfield@schoolnet-kx.org.au

Target Market(s)

Parents

Industry/Entity Type

Education

Contact Information for Business Card

Dale Owen Wrenfield
Principal
Tern Ridge Hill RCS
Phone: (08) 9170 3158
Fax: (08) 9170 3206
Mobile: 0488 613 947

Colors
f37122
000000

Requirements
Must have
• see breif

```html
<!DOCTYPE html>
<html lang="en">
<head>
<meta charset="utf-8">
<title>Tern Ridge Hill RCS – Stationery</title>
<link rel="stylesheet" href="https://fonts.googleapis.com/css2?family=Open+Sans:wght@400;600;700&display=swap">
<style>
  :root{
    --orange:#f37122;
    --black:#000000;
    --ink:#2b2b2b;
    --muted:#6a6a6a;
    --paper:#ffffff;
    --backdrop:#eeeeee;
  }
  *{box-sizing:border-box;margin:0;padding:0}
  html,body{width:1200px;height:778px;overflow:hidden}
  body{background:var(--backdrop);font-family:"Open Sans",Arial,sans-serif;color:var(--ink);position:relative}

  /* Letterhead */
  .letterhead{position:absolute;left:120px;top:66px;width:450px;height:640px;background:var(--paper);box-shadow:0 2px 10px rgba(0,0,0,.12);overflow:hidden}
  .letterhead__swoosh{position:absolute;left:0;bottom:0;width:450px;height:640px}
  .brand{position:absolute;left:34px;top:36px;display:flex;align-items:center;gap:8px}
  .brand__dot{width:22px;height:22px;border-radius:50%;background:var(--orange);flex:none}
  .brand__name{font-weight:700;font-size:13px;color:var(--ink);white-space:nowrap}
  .motto{position:absolute;left:64px;top:56px;font-size:6.5px;color:var(--muted)}
  .contact{position:absolute;right:34px;top:30px;list-style:none;font-size:7px;color:var(--ink);line-height:13px}
  .contact li{display:flex;align-items:center;gap:5px;white-space:nowrap}
  .icon{width:8px;height:8px;flex:none}
  .letter{position:absolute;left:34px;top:120px;width:360px;font-size:7px;line-height:11px;color:var(--ink)}
  .letter__to{margin-bottom:12px}
  .letter__to p:nth-child(2){font-weight:600}
  .letter__para{margin-bottom:9px;color:#444}
  .letter__close{margin-top:16px}
  .signature{width:72px;height:28px;margin:6px 0 2px;background:linear-gradient(90deg,#d9d9d9,#bdbdbd);border-radius:3px}
  .letter__signer{color:var(--muted)}

  /* Business cards */
  .card{position:absolute;width:340px;height:196px;overflow:hidden;box-shadow:0 2px 8px rgba(0,0,0,.15)}
  .card svg.card__art{position:absolute;inset:0;width:340px;height:196px}
  .card--back{left:700px;top:330px;background:var(--paper)}
  .card--front{left:620px;top:548px;background:var(--black)}
  .person{position:absolute;left:26px;top:48px}
  .person__name{font-weight:700;font-size:12px;color:var(--ink)}
  .person__role{font-size:8px;color:var(--muted)}
  .card .contact{right:auto;left:190px;top:24px;font-size:7px;line-height:13px}
  .card-brand{position:absolute;left:150px;top:96px;display:flex;align-items:center;gap:8px}
  .card-brand .brand__name{color:var(--paper);font-size:14px}
</style>
</head>
<body>

<section class="letterhead" aria-label="Letterhead">
  <svg class="letterhead__swoosh" viewBox="0 0 450 640" aria-hidden="true">
    <path d="M0,556 C150,526 300,474 430,398 C300,486 150,542 0,570Z" fill="var(--orange)"/>
    <path d="M0,574 C160,546 330,486 450,382 L450,640 L0,640Z" fill="var(--black)"/>
  </svg>

  <div class="brand"><span class="brand__dot"></span><span class="brand__name">Tern Ridge Hill RCS</span></div>
  <p class="motto">Learning Together on Country</p>

  <ul class="contact">
    <li><svg class="icon" viewBox="0 0 10 10"><path d="M2 1l2 2-1 1.5c.6 1.2 1.3 1.9 2.5 2.5L7 6l2 2-1.5 1.5C4 9 1 6 .5 2.5Z" fill="var(--ink)"/></svg>(08) 9170 3158</li>
    <li><svg class="icon" viewBox="0 0 10 10"><rect x="1" y="3" width="8" height="5" fill="var(--ink)"/><rect x="3" y="1" width="4" height="3" fill="var(--ink)"/></svg>(08) 9170 3206</li>
    <li><svg class="icon" viewBox="0 0 10 10"><circle cx="5" cy="5" r="4" fill="var(--ink)"/></svg>ABN 41 287 519 302</li>
    <li><svg class="icon" viewBox="0 0 10 10"><path d="M5 0a3.5 3.5 0 0 1 3.5 3.5C8.5 6 5 10 5 10S1.5 6 1.5 3.5A3.5 3.5 0 0 1 5 0Z" fill="var(--ink)"/></svg>PMB 4 Karrawin WA</li>
  </ul>

  <article class="letter">
    <div class="letter__to">
      <p>To,</p>
      <p>Ms. Harriet Colby</p>
      <p>Chief Executive Officer</p>
      <p>Colby Reed Studio</p>
      <p>12 Harbour Road</p>
      <p>Lake Mirren, WA 6999</p>
    </div>
    <p class="letter__para">We are pleased to share an update on the term ahead for our families and community. Classes resume on Monday with a full timetable, a new reading program and weekly visits from the health clinic. Please keep an eye on notices sent home with students.</p>
    <p class="letter__para">Our staff will hold an open morning in week three so parents can meet teachers, see student work and talk about goals for the year. Morning tea will be served in the school hall.</p>
    <p class="letter__para">Thank you for your ongoing support of our students and their learning.</p>
    <p class="letter__close">Yours faithfully,</p>
    <div class="signature" role="img" aria-label="Handwritten signature"></div>
    <p class="letter__signer">Alan Pike Moss</p>
  </article>
</section>

<section class="card card--back" aria-label="Business card, contact side">
  <svg class="card__art" viewBox="0 0 340 196" aria-hidden="true">
    <path d="M0,176 C120,160 240,120 340,76 L340,84 C240,132 120,170 0,184Z" fill="var(--orange)"/>
    <path d="M0,188 C120,176 240,136 340,90 L340,196 L0,196Z" fill="var(--black)"/>
  </svg>
  <div class="person">
    <p class="person__name">Dale Owen Wrenfield</p>
    <p class="person__role">Principal</p>
  </div>
  <ul class="contact">
    <li><svg class="icon" viewBox="0 0 10 10"><path d="M2 1l2 2-1 1.5c.6 1.2 1.3 1.9 2.5 2.5L7 6l2 2-1.5 1.5C4 9 1 6 .5 2.5Z" fill="var(--ink)"/></svg>(08) 9170 3158</li>
    <li><svg class="icon" viewBox="0 0 10 10"><rect x="1" y="3" width="8" height="5" fill="var(--ink)"/><rect x="3" y="1" width="4" height="3" fill="var(--ink)"/></svg>(08) 9170 3206</li>
    <li><svg class="icon" viewBox="0 0 10 10"><rect x="2.5" y="0.5" width="5" height="9" rx="1" fill="var(--ink)"/></svg>0488 613 947</li>
    <li><svg class="icon" viewBox="0 0 10 10"><rect x="0.5" y="2" width="9" height="6" fill="var(--ink)"/><path d="M0.5 2 5 5.5 9.5 2" stroke="#fff" fill="none"/></svg>Dale.Wrenfield@schoolnet-kx.org.au</li>
    <li><svg class="icon" viewBox="0 0 10 10"><path d="M5 0a3.5 3.5 0 0 1 3.5 3.5C8.5 6 5 10 5 10S1.5 6 1.5 3.5A3.5 3.5 0 0 1 5 0Z" fill="var(--ink)"/></svg>PMB 4 Karrawin WA</li>
  </ul>
</section>

<section class="card card--front" aria-label="Business card, brand side">
  <svg class="card__art" viewBox="0 0 340 196" aria-hidden="true">
    <path d="M0,0 H226 C150,44 64,112 0,186Z" fill="var(--paper)"/>
    <path d="M226,0 H252 C162,52 72,122 0,196 L0,186 C64,112 150,44 226,0Z" fill="var(--orange)"/>
  </svg>
  <div class="card-brand"><span class="brand__dot"></span><span class="brand__name">Tern Ridge Hill RCS</span></div>
</section>

</body>
</html>
```